RWT Fittings Ltd Business Cards

We need a business card with our business logo. We provide window and door installations on high-rises in west coast British Colombia, Canada.

I would like my business information and details on one side of the card, and the other side the company name with logo

Target Market(s)

General Contractors

Industry/Entity Type

Construction

Contact Information for Business Card

one side i want my company name and logo in the dark theme logo that i provided

Requirements
Must have
• Marco Peltieri, 16045518293, RWTFittings@mailbox-demo.com, 1407-5194 Linden Row Burnaby BC, V5H 2K9, Owner & Manager

```html
<!DOCTYPE html>
<html lang="en">
<head>
<meta charset="utf-8">
<title>RWT Fittings Ltd — Business Cards</title>
<link rel="stylesheet" href="https://fonts.googleapis.com/css2?family=Montserrat:wght@600;700&family=Roboto:wght@400;500&display=swap">
<style>
  :root {
    --stage: #232323;
    --card-white: #ffffff;
    --brand-blue: #29a9e1;
    --brand-grey: #8c8c8c;
    --ink: #161616;
    --back-grey: #8f8f8f;
    --back-grey-light: #a3a3a3;
  }
  * { box-sizing: border-box; margin: 0; padding: 0; }
  html, body {
    width: 1200px; height: 780px; overflow: hidden;
    background: var(--stage);
  }
  .stage {
    position: relative; width: 1200px; height: 780px;
    display: flex; align-items: center; justify-content: center; gap: 40px;
  }
  .card {
    position: relative; width: 540px; height: 309px; overflow: hidden;
    box-shadow: 0 10px 30px rgba(0,0,0,.45);
  }

  /* Front */
  .card-front { background: var(--card-white); }
  .brand {
    position: absolute; left: 118px; top: 48px;
    display: flex; align-items: center; gap: 12px;
  }
  .brand-mark { width: 34px; height: 34px; background: var(--brand-grey); }
  .brand-name {
    font-family: "Montserrat", sans-serif; font-weight: 700;
    font-size: 30px; letter-spacing: 1px; color: var(--brand-blue);
    line-height: 1;
  }
  .person { position: absolute; left: 44px; top: 168px; }
  .person-name {
    font-family: "Montserrat", sans-serif; font-weight: 700;
    font-size: 27px; line-height: 1.1;
  }
  .person-first { color: var(--brand-blue); }
  .person-last { color: var(--brand-grey); }
  .person-role {
    font-family: "Montserrat", sans-serif; font-weight: 600;
    font-size: 14px; color: var(--ink); margin-top: 4px; padding-left: 84px;
  }
  .divider {
    position: absolute; left: 300px; top: 140px;
    width: 1.5px; height: 82px; background: var(--ink);
  }
  .contacts {
    position: absolute; left: 318px; top: 150px;
    font-family: "Roboto", sans-serif; font-size: 13.5px; color: var(--ink);
    list-style: none;
  }
  .contacts li { display: flex; align-items: center; gap: 8px; height: 24px; }
  .contacts svg { width: 14px; height: 14px; flex: none; }
  .address-band {
    position: absolute; left: 0; right: 0; top: 250px; height: 30px;
    background: var(--brand-blue);
    display: flex; align-items: center; padding-left: 96px;
    font-family: "Roboto", sans-serif; font-size: 15px; color: var(--card-white);
  }

  /* Back */
  .card-back { background: var(--back-grey); }
  .back-pattern {
    position: absolute; inset: 0;
    background: radial-gradient(ellipse at 30% 40%, var(--back-grey-light), var(--back-grey) 70%);
  }
  .back-brand {
    position: absolute; right: 40px; top: 156px;
    display: flex; align-items: center; gap: 7px;
  }
  .back-brand-mark { width: 16px; height: 16px; background: var(--card-white); }
  .back-brand-name {
    font-family: "Montserrat", sans-serif; font-weight: 700;
    font-size: 14px; letter-spacing: .5px; color: var(--card-white);
  }
</style>
</head>
<body>
<main class="stage">
  <section class="card card-front" aria-label="Business card front">
    <div class="brand">
      <span class="brand-mark"></span>
      <span class="brand-name">RWT FITTINGS LTD</span>
    </div>

    <div class="person">
      <p class="person-name"><span class="person-first">Marco</span> <span class="person-last">Peltieri</span></p>
      <p class="person-role">Owner &amp; Manager</p>
    </div>

    <div class="divider"></div>

    <ul class="contacts">
      <li>
        <svg viewBox="0 0 24 24" aria-hidden="true"><path fill="#29a9e1" d="M6.6 10.8a15.1 15.1 0 0 0 6.6 6.6l2.2-2.2a1 1 0 0 1 1-.25 11.4 11.4 0 0 0 3.6.57 1 1 0 0 1 1 1V20a1 1 0 0 1-1 1A17 17 0 0 1 3 4a1 1 0 0 1 1-1h3.5a1 1 0 0 1 1 1c0 1.25.2 2.45.57 3.57a1 1 0 0 1-.25 1z"/></svg>
        <span>1604 551 8293</span>
      </li>
      <li>
        <svg viewBox="0 0 24 24" aria-hidden="true"><path fill="#29a9e1" d="M3 5h18a1 1 0 0 1 1 1v12a1 1 0 0 1-1 1H3a1 1 0 0 1-1-1V6a1 1 0 0 1 1-1zm1 2.2V17h16V7.2l-8 5.3z"/></svg>
        <span>RWTFittings@mailbox-demo.com</span>
      </li>
    </ul>

    <div class="address-band">1407-5194 Linden Row Burnaby BC, V5H 2K9</div>
  </section>

  <section class="card card-back" aria-label="Business card back">
    <div class="back-pattern" role="img" aria-label="Embossed repeating brand pattern across the card back"></div>
    <div class="back-brand">
      <span class="back-brand-mark"></span>
      <span class="back-brand-name">RWT FITTINGS LTD</span>
    </div>
  </section>
</main>
</body>
</html>
```